Brightbay Orthodontics business card design

Need a business card design that reflects our re-branding (orthodontic office - braces) and a new partnership with a pediatric dental office. We would like to include "for adults and children" on the card as well so adults know they are welcome to get their braces here as well. Office design is modern and would like business card to reflect a modern type look. Here's the text we would like to be included on the card:

Darren Wolcott, DDS, MSD
5214 West Linden Avenue, Suite 204
Mansfield, TX 76991
555-418-2637
www.brightbayortho.example
info@brightbayortho.example

Can we add the following to the existing designs? Darren Wolcott, DDS, MSD 5214 West Linden Avenue, Suite 204 Mansfield, TX 76991 555-418-2637

Does anyone have any more vertical designs available? Thanks!

Dental

```html
<!DOCTYPE html>
<html lang="en">
<head>
<meta charset="utf-8">
<title>Brightbay Orthodontics – Business Card</title>
<link rel="stylesheet" href="https://fonts.googleapis.com/css2?family=Open+Sans:wght@400;600;700;800&display=swap">
<style>
  :root {
    --backdrop: #8a8782;
    --card-light: #f7f7f7;
    --card-shade: #dedede;
    --card-dark: #252525;
    --ink: #1e1e1e;
    --ink-soft: #555555;
    --yellow: #f1e000;
    --blue: #1e73b8;
    --magenta: #e5137f;
    --green: #6fae2c;
    --orange: #d2760c;
    --name-blue: #2a86cf;
    --icon-green: #4caf3a;
    --text-light: #e9e9e9;
  }
  * { margin: 0; padding: 0; box-sizing: border-box; }
  html, body { width: 1200px; height: 871px; overflow: hidden; }
  body {
    background: var(--backdrop);
    font-family: "Open Sans", Arial, sans-serif;
    position: relative;
  }
  .card {
    position: absolute;
    width: 560px;
    height: 320px;
    overflow: hidden;
    box-shadow: 0 10px 24px rgba(0,0,0,0.35);
  }
  .card--front {
    left: 40px; top: 90px;
    background: linear-gradient(160deg, var(--card-light) 0%, #ececec 60%, var(--card-shade) 100%);
  }
  .card--back {
    left: 600px; top: 461px;
    background: var(--card-dark);
  }
  .colour-band {
    display: flex;
    height: 12px;
    width: 100%;
  }
  .colour-band span { flex: 1; }
  .colour-band .yellow { background: var(--yellow); }
  .colour-band .blue { background: var(--blue); }
  .colour-band .magenta { background: var(--magenta); }
  .colour-band .green { background: var(--green); }
  .colour-band .orange { background: var(--orange); }
  .card--front .colour-band { position: absolute; bottom: 0; left: 0; }

  .brand {
    display: flex;
    align-items: center;
    gap: 14px;
    color: var(--ink);
    font-weight: 800;
  }
  .brand-dot {
    border-radius: 50%;
    background: var(--blue);
    flex: none;
  }
  .brand-name { line-height: 1.05; }
  .tagline {
    color: var(--ink-soft);
    font-weight: 600;
    letter-spacing: 1px;
    text-transform: uppercase;
    text-align: center;
    position: absolute;
    left: 0; right: 0;
  }
  .card--front .brand {
    position: absolute;
    left: 0; right: 0; top: 104px;
    justify-content: center;
  }
  .card--front .brand-dot { width: 54px; height: 54px; }
  .card--front .brand-name { font-size: 38px; }
  .card--front .tagline { top: 206px; font-size: 13px; }

  .back-top {
    height: 150px;
    background: linear-gradient(180deg, #ffffff 0%, #ececec 100%);
    position: relative;
  }
  .card--back .brand {
    position: absolute;
    left: 0; right: 0; top: 34px;
    justify-content: center;
  }
  .card--back .brand-dot { width: 32px; height: 32px; }
  .card--back .brand-name { font-size: 23px; }
  .card--back .tagline { top: 100px; font-size: 10px; }

  .person {
    position: absolute;
    left: 36px; top: 186px;
  }
  .person-name {
    color: var(--name-blue);
    font-weight: 700;
    font-size: 17px;
    letter-spacing: 0.5px;
  }
  .person-title {
    color: var(--text-light);
    font-size: 11px;
    margin-top: 2px;
  }
  .contact {
    position: absolute;
    left: 270px; top: 186px;
    color: var(--text-light);
    font-size: 12px;
    line-height: 18px;
  }
  .contact-address { margin-bottom: 10px; padding-left: 22px; }
  .contact-row {
    display: flex;
    align-items: center;
    gap: 10px;
  }
  .contact-row svg { width: 12px; height: 12px; flex: none; }
</style>
</head>
<body>

  <section class="card card--front" aria-label="Business card front">
    <div class="brand">
      <span class="brand-dot"></span>
      <span class="brand-name">Brightbay<br>Orthodontics</span>
    </div>
    <p class="tagline">For adults and children</p>
    <div class="colour-band">
      <span class="yellow"></span><span class="blue"></span><span class="magenta"></span><span class="green"></span><span class="orange"></span>
    </div>
  </section>

  <section class="card card--back" aria-label="Business card back">
    <div class="back-top">
      <div class="brand">
        <span class="brand-dot"></span>
        <span class="brand-name">Brightbay<br>Orthodontics</span>
      </div>
      <p class="tagline">For adults and children</p>
    </div>
    <div class="colour-band">
      <span class="yellow"></span><span class="blue"></span><span class="magenta"></span><span class="green"></span><span class="orange"></span>
    </div>

    <div class="person">
      <p class="person-name">Darren Wolcott</p>
      <p class="person-title">DDS, MSD</p>
    </div>

    <div class="contact">
      <p class="contact-address">5214 West Linden Avenue, Suite 204<br>Mansfield, TX 76991</p>
      <p class="contact-row">
        <svg viewBox="0 0 12 12" aria-hidden="true"><path fill="var(--icon-green)" d="M2.5 1h2l1 2.6-1.3 1a6.5 6.5 0 0 0 3.2 3.2l1-1.3L11 7.5v2c0 .8-.7 1.5-1.5 1.5A8.5 8.5 0 0 1 1 2.5C1 1.7 1.7 1 2.5 1z"/></svg>
        <span>555-418-2637</span>
      </p>
      <p class="contact-row">
        <svg viewBox="0 0 12 12" aria-hidden="true"><rect x="1" y="2.5" width="10" height="7" rx="1" fill="none" stroke="var(--icon-green)" stroke-width="1.3"/><path d="M1.5 3l4.5 3.5L10.5 3" fill="none" stroke="var(--icon-green)" stroke-width="1.3"/></svg>
        <span>info@brightbayortho.example</span>
      </p>
      <p class="contact-row">
        <svg viewBox="0 0 12 12" aria-hidden="true"><circle cx="6" cy="6" r="4.8" fill="none" stroke="var(--icon-green)" stroke-width="1.2"/><ellipse cx="6" cy="6" rx="2" ry="4.8" fill="none" stroke="var(--icon-green)" stroke-width="1"/><path d="M1.2 6h9.6" stroke="var(--icon-green)" stroke-width="1"/></svg>
        <span>www.brightbayortho.example</span>
      </p>
    </div>
  </section>

</body>
</html>
```